Automotive component supplier needs a business card design

We need a business card design for our company called Velran Global Components Ltd based in the UK. We are a supplier of interior and exterior components to premium car manufacturers such as Corvel Ashby, Hadley Fenn, Marquist and Tavarelli. We would like to see a modern business card design that uses the colour blue.

Target Market(s)

Premium automotive car manufacturers.

Industry/Entity Type

Automotive

Contact Information for Business Card

Company Name : Velran Global Components Limited
Address: 17 Marlow Yard, Upper Heath, Warwick, CV31 8QL, United Kingdom
Web Address : www.velrancomponents-example.co.uk

Font styles to use
Other font styles liked:
• Helvetica

Colors
3176b5
0255a3
85acd3
cfdeed
cee9f5
85cae6
34a6d7
0692cd
9bcb3c

Requirements
Must have
• Clear company logo and a mixture of blue colours.
Nice to have
• A high quality modern image.
Should not have
• Multiple colours.

```html
<!DOCTYPE html>
<html lang="en">
<head>
<meta charset="utf-8">
<title>Velran Global Components – Business Card</title>
<link href="https://fonts.googleapis.com/css2?family=Arimo:wght@400;700&display=swap" rel="stylesheet">
<style>
  :root {
    --brand-blue: #0287c8;
    --deep-blue: #0255a3;
    --accent-green: #9bcb3c;
    --card-white: #ffffff;
    --backdrop: #e4e6e9;
    --shadow: rgba(0, 0, 0, 0.28);
  }
  * { margin: 0; padding: 0; box-sizing: border-box; }
  html, body {
    width: 1200px;
    height: 843px;
    overflow: hidden;
    background: var(--backdrop);
    font-family: "Arimo", Helvetica, Arial, sans-serif;
  }
  .stage {
    position: relative;
    width: 1200px;
    height: 843px;
  }
  .card {
    position: absolute;
    top: 252px;
    width: 558px;
    height: 319px;
    background: var(--card-white);
    box-shadow: 0 3px 8px var(--shadow);
    overflow: hidden;
  }
  .card--front { left: 28px; }
  .card--back { left: 613px; }

  /* brand block */
  .brand {
    color: var(--brand-blue);
    font-weight: 700;
    line-height: 1;
  }
  .brand__name {
    display: flex;
    align-items: center;
    gap: 8px;
    font-size: 38px;
    letter-spacing: 2px;
  }
  .brand__dot {
    width: 9px;
    height: 9px;
    background: var(--accent-green);
    border-radius: 2px;
  }
  .brand__tagline {
    font-size: 11px;
    letter-spacing: 1.2px;
    margin-top: 5px;
  }

  /* front card */
  .card--front .brand {
    position: absolute;
    left: 23px;
    top: 52px;
  }
  .contact {
    position: absolute;
    left: 24px;
    top: 120px;
    color: var(--brand-blue);
  }
  .contact__name {
    font-weight: 700;
    font-size: 17px;
    letter-spacing: 1.4px;
  }
  .contact__role {
    color: var(--accent-green);
    font-size: 14px;
    margin-top: 3px;
  }
  .contact__address {
    font-size: 14px;
    line-height: 18px;
    margin-top: 9px;
  }
  .contact__list {
    list-style: none;
    margin-top: 9px;
    font-size: 14px;
    line-height: 17.6px;
  }
  .contact__list li {
    display: flex;
    align-items: center;
    gap: 9px;
  }
  .contact__list svg {
    width: 10px;
    height: 10px;
    flex: none;
  }

  .band {
    position: absolute;
    top: 0;
    height: 100%;
    width: 110px;
    background: var(--brand-blue);
  }
  .card--front .band { right: 0; }
  .card--back .band { left: 0; }

  /* back card */
  .card--back .brand {
    position: absolute;
    right: 24px;
    top: 128px;
    text-align: right;
  }
  .card--back .brand__name { justify-content: flex-end; font-size: 40px; }
  .card--back .brand__tagline { font-size: 12px; }
  .web {
    position: absolute;
    right: 24px;
    bottom: 20px;
    font-size: 13.5px;
    color: var(--brand-blue);
  }
  .web__mid { color: var(--accent-green); }
</style>
</head>
<body>
<main class="stage">

  <section class="card card--front" aria-label="Business card front">
    <div class="brand">
      <div class="brand__name"><span>VELRAN</span><span class="brand__dot"></span></div>
      <div class="brand__tagline">GLOBAL COMPONENTS</div>
    </div>

    <div class="contact">
      <p class="contact__name">LINDEN ASHGROVE</p>
      <p class="contact__role">Director</p>
      <p class="contact__address">17 Marlow Yard, Upper Heath<br>Warwick, CV31 8QL, UK</p>
      <ul class="contact__list">
        <li>
          <svg viewBox="0 0 10 10" aria-hidden="true"><path d="M2 0.5 L3.6 2.8 L2.8 3.8 Q4 6.2 6.2 7.2 L7.2 6.4 L9.5 8 L8.5 9.5 Q2 9 0.5 1.5 Z" fill="#9bcb3c"/></svg>
          780 612-3048
        </li>
        <li>
          <svg viewBox="0 0 10 10" aria-hidden="true"><rect x="2.5" y="0.5" width="5" height="9" rx="1" fill="none" stroke="#9bcb3c" stroke-width="1.2"/><rect x="4.3" y="7.4" width="1.4" height="1" fill="#9bcb3c"/></svg>
          780 612-3191
        </li>
        <li>
          <svg viewBox="0 0 10 10" aria-hidden="true"><rect x="0.5" y="2" width="9" height="6" fill="#9bcb3c"/><path d="M0.5 2 L5 5.5 L9.5 2" fill="none" stroke="#ffffff" stroke-width="1"/></svg>
          velran@example-mail.com
        </li>
        <li>
          <svg viewBox="0 0 10 10" aria-hidden="true"><g fill="none" stroke="#9bcb3c" stroke-width="0.9"><circle cx="5" cy="5" r="4.3"/><ellipse cx="5" cy="5" rx="1.8" ry="4.3"/><path d="M0.7 5 H9.3 M1.5 2.8 H8.5 M1.5 7.2 H8.5"/></g></svg>
          www.velrancomponents-example.co.uk
        </li>
      </ul>
    </div>

    <div class="band"></div>
  </section>

  <section class="card card--back" aria-label="Business card back">
    <div class="band"></div>
    <div class="brand">
      <div class="brand__name"><span>VELRAN</span><span class="brand__dot"></span></div>
      <div class="brand__tagline">GLOBAL COMPONENTS</div>
    </div>
    <p class="web">www.<span class="web__mid">velrancomponents-example</span>.co.uk</p>
  </section>

</main>
</body>
</html>
```